Health Clinic treating people with mental illness needs a website

We need a website for a new mental health clinic based in Florida called Solvane Wellness USA. We treat people with mental health issues such as depression, PTSD, Bipolar, chronic pain, etc. I want the website to be easy to follow and inviting to the visitors. It should be easy to locate the different treatment options and how to go about contacting and making appointments. The images on the website should be something that the patients can relate to, whether a close up of a woman's face, something that conveys emotion. The patients visiting this website are often sad and miserable, they need to be able to feel comfortable when they look at this website. I want them to feel that we understand where they are coming from. I like colors such as purple, turquoise, lavender.

Target Market(s)

College students, veterans, anyone with mental illness

Industry/Entity Type

Health And Wellness

Font styles to use
Serif
Sans Serif

Colors

Designer to choose colors to be used in the design.

Requirements
Must have
• There should be a home/landing page, about us page, treatment page, contact page, and a FAQ page. I've included my logo below.
Nice to have
• The flow of the web pages should be calming and welcoming. I want people to feel warm and understood when they enter our page.
Should not have
• The images and writing should not be overly stimulating or aggressive.

```html
<!DOCTYPE html>
<html lang="en">
<head>
<meta charset="utf-8">
<title>Solvane Wellness USA — Mental Health Clinic</title>
<link href="https://fonts.googleapis.com/css2?family=Dosis:wght@300;400;500;600;700;800&family=Open+Sans:ital,wght@0,400;0,600;1,400&display=swap" rel="stylesheet">
<style>
:root{
  --teal:#2eac90;
  --teal-soft:#79c8b8;
  --teal-form:#46b49a;
  --purple:#8d2a87;
  --purple-deep:#5a2070;
  --ink:#1f1f22;
  --muted:#4a4a4a;
  --grey-bg:#ececec;
  --white:#ffffff;
}
*{box-sizing:border-box;margin:0;padding:0}
html,body{width:1200px;height:3634px;overflow:hidden}
body{position:relative;background:var(--white);font-family:"Open Sans",sans-serif;color:var(--ink)}
.abs{position:absolute}
.heading{font-family:"Dosis",sans-serif;font-weight:700;text-transform:uppercase}
.btn{display:flex;align-items:center;justify-content:center;font-family:"Dosis",sans-serif;font-weight:700;text-transform:uppercase;color:var(--white)}

/* top bar */
.topbar{left:0;top:0;width:1200px;height:31px;background:var(--teal);color:var(--white);font-family:"Dosis",sans-serif;font-weight:600;font-size:16px;display:flex;align-items:center;justify-content:center;letter-spacing:.3px}

/* header */
.header{left:0;top:31px;width:1200px;height:100px;background:var(--white);border-bottom:2px solid #e2e2e2}
.brand{left:156px;top:64px;display:flex;align-items:center;gap:10px;font-family:"Dosis",sans-serif;font-weight:700;font-size:26px;line-height:34px;color:var(--purple-deep)}
.brand .dot{width:14px;height:14px;border-radius:50%;background:var(--purple-deep)}
.nav{left:434px;top:71px;display:flex;gap:29px;font-family:"Dosis",sans-serif;font-weight:600;font-size:16px;line-height:22px;color:var(--ink)}
.nav .active{color:var(--purple)}
.nav-cta{left:869px;top:65px;width:186px;height:36px;background:var(--purple);font-size:14px}

/* hero */
.hero{left:0;top:131px;width:1200px;height:604px;background:linear-gradient(180deg,#d3d6d9 0%,#a9b0b5 22%,#6f7b82 36%,#7c8891 60%,#6b7680 100%)}
.hero-form{left:145px;top:244px;width:350px;height:350px;background:var(--teal-form);border-radius:26px;opacity:.95}
.field{left:169px;width:302px;height:44px;background:var(--white);border:1px solid #dcdcdc;font-size:13px;color:#555;padding-left:15px;display:flex;align-items:center;font-family:"Dosis",sans-serif;font-weight:500}
.field svg{position:absolute;right:14px;top:17px}
.hero-submit{left:170px;top:512px;width:301px;height:44px;background:var(--purple);font-size:17px;border-radius:2px}
.hero-title{left:560px;top:488px;width:430px;text-align:center;color:var(--white)}
.hero-title h1{font-family:"Dosis",sans-serif;font-weight:700;font-size:44px;line-height:1.05;text-transform:uppercase}
.hero-title p{font-family:"Dosis",sans-serif;font-weight:300;font-size:38px;line-height:1.15}

/* welcome */
.welcome-photo{left:145px;top:853px;width:585px;height:423px;background:linear-gradient(120deg,#f2f2f0 0%,#c9c6c2 45%,#8a8a8e 100%)}
.welcome-card{left:551px;top:1000px;width:505px;height:338px;background:var(--teal-soft);color:var(--white)}
.welcome-card .kicker{position:absolute;left:40px;top:36px;font-family:"Dosis",sans-serif;font-weight:400;font-size:23px}
.welcome-card h2{position:absolute;left:40px;top:64px;font-family:"Dosis",sans-serif;font-weight:700;font-size:39px}
.welcome-card p{position:absolute;left:40px;top:120px;width:440px;font-size:13.5px;line-height:28.5px}
.read-more{left:551px;top:1290px;width:141px;height:48px;background:var(--teal);font-size:14px}

/* treatment */
.treatment{left:0;top:1444px;width:1200px;height:688px;background:linear-gradient(90deg,#ebebeb,#f3f3f3 50%,#e9e9e9)}
.section-title{width:1200px;text-align:center;font-size:33px;color:var(--ink);font-family:"Dosis",sans-serif;font-weight:700;text-transform:uppercase}
.card{top:1592px;width:285px;height:385px;background:#fafafa;border:1px solid #dedede;box-shadow:0 1px 3px rgba(0,0,0,.08)}
.card .photo{height:183px}
.card h3{margin-top:26px;text-align:center;font-family:"Dosis",sans-serif;font-weight:700;font-size:16px;text-transform:uppercase}
.card p{margin:12px auto 0;width:240px;text-align:center;font-size:13.5px;line-height:24px;color:var(--muted)}
.card .btn{margin:14px auto 0;width:117px;height:32px;background:var(--purple);font-size:13px}
.view-more{left:508px;top:2022px;width:186px;height:37px;background:var(--teal);font-size:13px}

/* testimonials */
.quote{width:260px;text-align:center}
.avatar{margin:0 auto;width:86px;height:86px;border-radius:50%;position:relative}
.avatar .mark{position:absolute;left:31px;bottom:-12px;width:24px;height:24px;border-radius:50%;background:var(--teal);display:flex;align-items:center;justify-content:center}
.quote p{margin-top:34px;font-size:13.5px;line-height:24px;color:var(--muted)}
.quote .name{margin-top:15px;font-style:italic;color:var(--teal);font-size:14px}

/* banner */
.banner{left:0;top:2647px;width:1200px;height:455px;background:linear-gradient(120deg,#5fbf8f 0%,#8fd7a8 45%,#b9e3b2 65%,#4fb091 100%)}
.banner-brand{left:0;top:2805px;width:1200px;text-align:center;font-family:"Dosis",sans-serif;font-weight:600;font-size:46px;color:var(--white)}
.banner-title{left:0;top:2888px;width:1200px;text-align:center;font-size:46px;color:var(--white)}

/* contact */
.contact-left{left:0;top:3102px;width:598px;height:439px;background:linear-gradient(120deg,#9b3b94,#8d2a87 60%,#7a2a83)}
.contact-left h2{position:absolute;left:145px;top:90px;font-family:"Dosis",sans-serif;font-weight:700;font-size:29px;color:var(--white)}
.contact-info{position:absolute;left:145px;top:155px;font-family:"Dosis",sans-serif;font-size:14px;line-height:23px;color:var(--white)}
.contact-info p+p{margin-top:12px}
.contact-right{left:598px;top:3102px;width:602px;height:439px;background:#f5f4f6}
.in{width:178px;border-bottom:1px solid #555;font-family:"Dosis",sans-serif;font-size:14px;color:#333;padding-bottom:8px}
.submit{left:656px;top:3379px;width:393px;height:43px;background:var(--purple);font-size:16px}

/* footer */
.footer{left:0;top:3541px;width:1200px;height:93px;background:var(--grey-bg);display:flex;align-items:center;justify-content:center;font-family:"Dosis",sans-serif;font-size:14px;color:#333}
</style>
</head>
<body>

<div class="abs topbar">Call Us : 555 0140 3172</div>

<header class="abs header"></header>
<div class="abs brand"><span class="dot"></span>Solvane Wellness USA</div>
<nav class="abs nav">
  <span class="active">HOME</span><span>ABOUT US</span><span>TREATMENT</span><span>FAQ</span><span>CONTACT US</span>
</nav>
<div class="abs btn nav-cta">Make an appointment</div>

<section class="abs hero" role="img" aria-label="Photo of a woman looking out over a calm lake toward wooded hills"></section>
<div class="abs hero-form"></div>
<div class="abs field" style="top:281px">First Name</div>
<div class="abs field" style="top:337px">Email</div>
<div class="abs field" style="top:393px">Phone</div>
<div class="abs field" style="top:449px">Treatment
  <svg width="10" height="7" viewBox="0 0 10 7"><path d="M1 1l4 4 4-4" fill="none" stroke="#444" stroke-width="1.5"/></svg>
</div>
<div class="abs btn hero-submit">Make an appointment</div>
<div class="abs hero-title">
  <h1>Solvane Wellness</h1>
  <p>mental health clinic</p>
</div>

<div class="abs welcome-photo" role="img" aria-label="Photo of a counselling session between two women in a bright room"></div>
<div class="abs welcome-card">
  <span class="kicker">Welcome to</span>
  <h2 class="heading">Solvane Wellness</h2>
  <p>Sed ut perspiciatis unde omnis iste natus error sit voluptatem accusantium doloremque laudantium, totam rem aperiam, eaque ipsa quae ab illo inventore veritatis et quasi architecto beatae vitae dicta sunt explicabo. Nemo enim ipsam voluptatem quia voluptas sit aspernatur aut odit aut fugit</p>
</div>
<div class="abs btn read-more">Read more</div>

<section class="abs treatment" role="img" aria-label="Faded photo backdrop of a calm interior"></section>
<h2 class="abs section-title" style="left:0;top:1515px">Our Treatment</h2>

<article class="abs card" style="left:145px">
  <div class="photo" role="img" aria-label="Photo of a woman resting her head in her hands at a table" style="background:linear-gradient(135deg,#d9dbd5,#9aa29a 60%,#c8c3bb)"></div>
  <h3>Depression</h3>
  <p>Sed ut perspiciatis unde omnis iste natus sit voluptatem accusantium doloremque laudantium</p>
  <div class="btn">Learn more</div>
</article>
<article class="abs card" style="left:460px">
  <div class="photo" role="img" aria-label="Photo of a woman shown with several contrasting expressions" style="background:linear-gradient(135deg,#3a3d3f,#8f8a80 55%,#2e3032)"></div>
  <h3>Bipolar</h3>
  <p>Sed ut perspiciatis unde omnis iste natus sit voluptatem accusantium doloremque laudantium</p>
  <div class="btn">Learn more</div>
</article>
<article class="abs card" style="left:773px">
  <div class="photo" role="img" aria-label="Photo of a person holding their lower back on a country path" style="background:linear-gradient(135deg,#b7893c,#d8b77a 45%,#6f86a8)"></div>
  <h3>Chronic Pain</h3>
  <p>Sed ut perspiciatis unde omnis iste natus sit voluptatem accusantium doloremque laudantium</p>
  <div class="btn">Learn more</div>
</article>
<div class="abs btn view-more">View more treatment</div>

<h2 class="abs section-title" style="left:0;top:2205px">Testimonials</h2>

<div class="abs quote" style="left:160px;top:2305px">
  <div class="avatar" role="img" aria-label="Portrait of a client" style="background:linear-gradient(135deg,#b9a89a,#6a5a4f)"><span class="mark"><svg width="12" height="10" viewBox="0 0 12 10"><path d="M0 10V6C0 2.5 2 .5 5 0v2C3.5 2.5 3 3.5 3 5h2v5zM7 10V6c0-3.5 2-5.5 5-6v2c-1.5.5-2 1.5-2 3h2v5z" fill="#fff"/></svg></span></div>
  <p>Sed ut perspiciatis unde omnis iste natus error sit voluptatem accusantium doloremque laudantium, totam rem aperiam, eaque ipsa quae ab</p>
  <div class="name">Morel, J.</div>
</div>
<div class="abs quote" style="left:469px;top:2305px">
  <div class="avatar" role="img" aria-label="Portrait of a client" style="background:linear-gradient(135deg,#c4c4c8,#4c4f58)"><span class="mark"><svg width="12" height="10" viewBox="0 0 12 10"><path d="M0 10V6C0 2.5 2 .5 5 0v2C3.5 2.5 3 3.5 3 5h2v5zM7 10V6c0-3.5 2-5.5 5-6v2c-1.5.5-2 1.5-2 3h2v5z" fill="#fff"/></svg></span></div>
  <p style="margin-top:32px">Sed ut perspiciatis unde omnis iste natus error sit voluptatem accusantium doloremque laudantium, totam rem aperiam, eaque ipsa quae ab</p>
  <div class="name">Morel, J.</div>
</div>
<div class="abs quote" style="left:781px;top:2305px">
  <div class="avatar" role="img" aria-label="Portrait of a client" style="background:linear-gradient(135deg,#9fb2c9,#3e4658)"><span class="mark"><svg width="12" height="10" viewBox="0 0 12 10"><path d="M0 10V6C0 2.5 2 .5 5 0v2C3.5 2.5 3 3.5 3 5h2v5zM7 10V6c0-3.5 2-5.5 5-6v2c-1.5.5-2 1.5-2 3h2v5z" fill="#fff"/></svg></span></div>
  <p>Sed ut perspiciatis unde omnis iste natus error sit voluptatem accusantium doloremque laudantium, totam rem aperiam, eaque ipsa quae ab</p>
  <div class="name">Morel, J.</div>
</div>

<section class="abs banner" role="img" aria-label="Photo of a woman with arms open wide in sunlight, tinted green"></section>
<div class="abs banner-brand">Solvane Wellness USA</div>
<h2 class="abs heading banner-title">Mental Health Clinic</h2>

<section class="abs contact-left" role="img" aria-label="Purple-tinted photo of a smiling woman">
  <h2>GET IN TOUCH</h2>
  <div class="contact-info">
    <p>I'm a paragraph. Click here to add your<br>own text and edit me.</p>
    <p>Address. 214 Harbor Light Lane<br>Tampa, FL 33602</p>
    <p>Email. hello@solvanewellness.com<br>Phone. 555-0193-4471</p>
  </div>
</section>
<section class="abs contact-right"></section>
<div class="abs in" style="left:656px;top:3199px">First Name</div>
<div class="abs in" style="left:871px;top:3199px">Last Name</div>
<div class="abs in" style="left:656px;top:3255px">Email</div>
<div class="abs in" style="left:871px;top:3255px">Subject</div>
<div class="abs in" style="left:656px;top:3311px;width:393px">Type your message here...</div>
<div class="abs btn submit">Submit</div>

<footer class="abs footer">(c) 2019 Solvane Wellness | All Rights Reserved | Disclaimer</footer>

</body>
</html>
```